Korvath Supply Website Redesign

Currently korvathsupply.example is focussed on fulfillment and transport from various products in the BBQ segment. However, no we want to update our business activities to Product Development, Brand Development, Online Positioning, Logistics & Aftersales, and Promotional BBQs. We will be a business for Outdoor Leisure Development from A to Z.

Therefore, we need a brand new website. The colours of the current website may be the same. However, i'd like to keep it clean. More white and use blue and green as accent colours. It is a business to business organization so the website should be looking formal and corporate. However we sell fun products so not too formal and corporate.

Pages we need; Home, About, Contact, Our Services (+ page per service) a place to share our news/blogs.

I have added some sort of mock up of an idea. However it needs some finetuning.

Target Market(s)

Businesses

Industry/Entity Type

Corporate/Logistics/Marketing

Coding

Coded - Design and coding required

Colors

Designer to choose colors to be used in the design.

Requirements
Must have
• Show clear distinguishing of the different services we provide (Product Development, Brand Development, Online Positioning, Logistics & Aftersales and Promotional BBQs). Every service should have its own page too. Besides, I would like to have a blog page to share relevant content.
Nice to have
• Show that we are the expert in Outdoor LEisure Development from A to Z
Should not have
• Be too informal. It may be semi-formal

```html
<!DOCTYPE html>
<html lang="en">
<head>
<meta charset="utf-8">
<title>Korvath Supply — Outdoor Leisure Development</title>
<link href="https://fonts.googleapis.com/css2?family=Poppins:wght@300;400;500;600;700;800&display=swap" rel="stylesheet">
<style>
:root{
  --teal:#2f5f6b;
  --teal-dark:#244c56;
  --green:#3b9c3b;
  --green-soft:#e3f1e3;
  --ink:#1d2a31;
  --muted:#6b7479;
  --line:#d9dde0;
  --panel:#eef0f3;
  --card:#edf0f8;
  --white:#ffffff;
}
*{box-sizing:border-box;margin:0;padding:0}
html,body{width:1200px;height:4971px;overflow:hidden}
body{font-family:"Poppins",sans-serif;color:var(--ink);background:var(--white);position:relative}
.abs{position:absolute}
a{color:inherit;text-decoration:none}

/* top bar */
.topbar{top:0;left:0;width:1200px;height:50px;background:var(--teal);color:#fff;font-size:13px}
.topbar .login{position:absolute;right:0;top:0;height:50px;width:341px;background:var(--green);clip-path:polygon(30px 0,100% 0,100% 100%,0 100%)}
.topbar span{position:absolute;top:16px;display:flex;align-items:center;gap:7px}
.dot{display:inline-block;width:12px;height:12px;border-radius:50%;background:#fff}

/* header */
.header{top:50px;left:0;width:1200px;height:104px;background:#fff}
.brand{position:absolute;left:110px;top:24px;display:flex;align-items:center;gap:12px;font-weight:700;font-size:42px;color:var(--teal);letter-spacing:.5px}
.brand i{width:34px;height:34px;border-radius:50%;background:var(--green);display:block}
.nav{position:absolute;top:50px;font-size:15px;color:var(--ink)}

/* hero */
.hero{top:154px;left:0;width:1200px;height:700px;background:linear-gradient(100deg,#3d3a35 0%,#6d6256 45%,#b79e86 70%,#8e7a6a 100%)}
.hero h1{position:absolute;left:110px;top:170px;color:#fff;font-size:54px;line-height:64px;font-weight:700}
.hero h1 span{font-weight:300;display:block}
.hero p{position:absolute;left:110px;top:314px;width:470px;color:#fff;font-size:13.5px;line-height:30px}
.btn{display:flex;align-items:center;justify-content:center;gap:10px;background:var(--teal);color:#fff;font-weight:600;font-size:15px;border-radius:4px;box-shadow:0 4px 10px rgba(0,0,0,.2)}
.btn b{width:14px;height:14px;border-radius:50%;background:#fff;position:relative}
.btn b:after{content:"";position:absolute;left:4px;top:4px;border-left:6px solid var(--teal);border-top:3px solid transparent;border-bottom:3px solid transparent}
.slide-no{position:absolute;left:30px;color:#fff;font-size:14px}
.slide-line{position:absolute;left:37px;top:240px;width:2px;height:200px;background:#fff}
.dots{position:absolute;left:515px;top:628px;display:flex;gap:20px}
.dots i{width:54px;height:4px;background:#fff;display:block}
.dots i:first-child{background:var(--green)}

/* section headings */
.heading{font-weight:700;font-size:40px;position:absolute;z-index:1}
.heading:before{content:"";position:absolute;left:-28px;top:-14px;width:78px;height:78px;border-radius:50%;background:var(--green-soft);z-index:-1}
.center{left:0;width:1200px;text-align:center}
.center .h-in{position:relative;display:inline-block}
.center .h-in:before{content:"";position:absolute;left:-28px;top:-14px;width:78px;height:78px;border-radius:50%;background:var(--green-soft);z-index:-1}
.center.heading:before{display:none}

/* about */
.about-photo{left:108px;top:974px;width:464px;height:464px;border-radius:50%;background:radial-gradient(circle at 50% 45%,#d7a14a 0%,#8a6a45 40%,#3d4e7a 75%,#2b3558 100%);border:8px solid #fff;box-shadow:0 6px 22px rgba(0,0,0,.18)}
.about-text{left:600px;width:490px;font-size:13.5px;line-height:30px;color:var(--muted)}

/* services */
.services{top:1515px;left:0;width:1200px;height:755px;background:var(--teal)}
.card{position:absolute;top:189px;width:300px;height:455px;background:#fff;clip-path:polygon(0 0,100% 0,100% 92%,0 100%)}
.card .img{height:240px}
.card .icon{position:absolute;left:116px;top:206px;width:68px;height:68px;border-radius:50%;background:var(--green);border:5px solid #fff;display:flex;align-items:center;justify-content:center}
.card h3{position:absolute;top:290px;width:100%;text-align:center;font-size:16px;font-weight:600}
.card p{position:absolute;top:322px;left:20px;right:20px;text-align:center;font-size:13px;line-height:27px;color:var(--muted)}
.arrow{position:absolute;top:406px;width:50px;height:50px;border-radius:50%;border:2px solid #fff;display:flex;align-items:center;justify-content:center}

/* special */
.special{top:2270px;left:0;width:1200px;height:770px;background:var(--panel)}
.special p{position:absolute;left:180px;width:840px;top:172px;text-align:center;font-size:14.5px;line-height:31px;color:var(--muted)}
.special .img{position:absolute;left:0;top:316px;width:1200px;height:454px;background:radial-gradient(ellipse at 50% 45%,#8f9499 0%,#c9ccd0 30%,#eceef1 60%,#eef0f3 100%)}

/* blog */
.blog-big{left:110px;top:3275px;width:463px;height:585px;background:#fff;box-shadow:0 4px 18px rgba(0,0,0,.12)}
.blog-big .img{height:301px;background:linear-gradient(135deg,#3a0d0a,#a3341a 45%,#e07a2c 70%,#2d0b08)}
.pill{position:absolute;background:var(--teal);color:#fff;font-size:13px;padding:0 24px;height:36px;line-height:36px;border-radius:0 20px 20px 0}
.blog-big h4{position:absolute;left:28px;right:24px;top:390px;font-size:16px;font-weight:500;line-height:28px}
.blog-big p{position:absolute;left:28px;right:24px;top:450px;font-size:12px;line-height:26px;color:var(--muted)}
.more{position:absolute;font-size:13px;font-weight:600;color:var(--green);border-bottom:1px solid var(--green)}
.blog-sm{left:600px;width:487px;height:272px;background:var(--card)}
.blog-sm .img{position:absolute;left:0;top:0;width:230px;height:100%}
.blog-sm .pill{left:230px;top:22px;height:30px;line-height:30px;font-size:12px;padding:0 20px}
.blog-sm h4{position:absolute;left:245px;right:15px;top:74px;font-size:13px;font-weight:500;line-height:24px}
.blog-sm p{position:absolute;left:245px;right:15px;top:128px;font-size:11px;line-height:26px;color:var(--muted)}

/* partners */
.partner{position:absolute;top:4262px;font-size:34px;font-weight:700;color:#3a3f44;display:flex;align-items:center;gap:10px}
.partner i{width:26px;height:26px;display:block;background:#3a3f44}

/* footer */
.map{top:4425px;left:0;width:359px;height:546px;background:linear-gradient(160deg,#e8ecef,#d5dde3 50%,#e4e9ec)}
.addr{left:42px;top:4564px;width:263px;height:103px;background:#fff;box-shadow:0 2px 8px rgba(0,0,0,.2);padding:14px 12px;font-size:13px;line-height:24px}
.contact{top:4425px;left:359px;width:482px;height:546px;background:var(--teal);color:#fff}
.contact h2{position:absolute;top:46px;width:100%;text-align:center;font-size:23px;font-weight:700}
.field{position:absolute;left:46px;width:392px;height:20px;border-bottom:1px solid rgba(255,255,255,.7);font-size:14px}
.submit{position:absolute;left:152px;top:301px;width:180px;height:48px;background:var(--green);border-radius:3px;color:#fff;font-weight:700;font-size:16px;display:flex;align-items:center;justify-content:center;box-shadow:0 3px 8px rgba(0,0,0,.25)}
.contact .line{position:absolute;width:100%;text-align:center;font-size:15px}
.side{top:4425px;left:841px;width:359px;height:546px;background:linear-gradient(150deg,#3b4650,#5b6770 45%,#2e363d)}
.copy{left:862px;top:4928px;color:#fff;font-size:14px}
</style>
</head>
<body>

<!-- Top bar -->
<div class="abs topbar">
  <div class="login"></div>
  <span style="left:110px"><i class="dot"></i>English ⌄</span>
  <span style="left:425px">
    <svg width="12" height="12" viewBox="0 0 24 24"><path fill="#fff" d="M6.6 10.8a15 15 0 0 0 6.6 6.6l2.2-2.2a1 1 0 0 1 1-.25 11.4 11.4 0 0 0 3.6.57 1 1 0 0 1 1 1V20a1 1 0 0 1-1 1A17 17 0 0 1 3 4a1 1 0 0 1 1-1h3.5a1 1 0 0 1 1 1c0 1.25.2 2.45.57 3.6a1 1 0 0 1-.25 1z"/></svg>
    Phone: +31 (0)10 555 0148</span>
  <span style="left:637px">
    <svg width="13" height="10" viewBox="0 0 26 20"><rect x="1" y="1" width="24" height="18" fill="#fff"/><path d="M1 1l12 10L25 1" fill="none" stroke="#2f5f6b" stroke-width="2"/></svg>
    info@korvathsupply.example</span>
  <span style="left:903px">
    <svg width="11" height="12" viewBox="0 0 22 24"><circle cx="11" cy="6" r="6" fill="#fff"/><path d="M0 24c0-7 5-10 11-10s11 3 11 10z" fill="#fff"/></svg>
    Login/Signup</span>
  <span style="left:1046px;gap:14px"><i class="dot"></i><i class="dot"></i></span>
</div>

<!-- Header -->
<header class="abs header">
  <div class="brand"><i></i>Korvath</div>
  <a class="nav" style="left:640px">Home</a>
  <a class="nav" style="left:727px">About</a>
  <a class="nav" style="left:814px">Our Services</a>
  <a class="nav" style="left:951px">Blog</a>
  <a class="nav" style="left:1025px">Contact</a>
</header>

<!-- Hero -->
<section class="abs hero" role="img" aria-label="Smiling woman paying online with a bank card at a laptop on a wooden table">
  <span class="slide-no" style="top:206px">01</span>
  <span class="slide-line"></span>
  <span class="slide-no" style="top:470px">04</span>
  <h1>E-Commerce &amp;<span>Order Portals</span></h1>
  <p>We believe that the partners we work for should be able to focus on building their brand and product. Korvath Supply therefore takes care of the process from order processing to delivery. Together with our Partner Korvath Promotional.</p>
  <a class="btn" style="position:absolute;left:110px;top:463px;width:180px;height:50px">Get Started <b></b></a>
  <div class="dots"><i></i><i></i><i></i><i></i></div>
</section>
<svg class="abs" style="left:0;top:800px" width="1200" height="90" viewBox="0 0 1200 90">
  <polygon points="0,90 0,78 850,28 1200,16 1200,90" fill="#fff"/>
  <polygon points="0,50 850,20 850,28 0,78" fill="#3b9c3b"/>
</svg>

<!-- About -->
<div class="abs about-photo" role="img" aria-label="Warehouse worker driving an orange forklift between tall stocked shelves"></div>
<h2 class="heading" style="left:621px;top:1002px">About Us</h2>
<p class="abs about-text" style="top:1089px">Lorem ipsum dolor sit amet, consectetur adipiscing elit, eiusmod tempor incididunt ut labore et dolore magna aliqua. Ut enim ad minim veniam, quis nostrud exercitation ullamco laboris nisi ut aliquip ex ea commodo consequat. Duis aute irure dolor in voluptate velit cillum dolore eu fugiat nulla pariatur. Excepteur sint occaecat cupidatat non proident, sunt in culpa qui officia deserunt</p>
<p class="abs about-text" style="top:1286px">Lorem ipsum dolor sit amet, consectetur adipiscing elit, eiusmod tempor incididunt ut labore et dolore magna aliqua.</p>
<a class="abs btn" style="left:600px;top:1374px;width:180px;height:50px">Read More <b></b></a>

<!-- Services -->
<section class="abs services">
  <svg class="abs" style="left:0;top:0" width="1200" height="755" viewBox="0 0 1200 755">
    <polygon points="600,16 1200,42 1200,58 600,28" fill="#3b9c3b"/>
    <polygon points="0,0 1200,0 1200,42 600,16 0,16" fill="#fff"/>
    <polygon points="0,728 600,736 600,755 0,755" fill="#fff"/>
    <polygon points="0,717 600,730 600,740 0,734" fill="#3b9c3b"/>
    <polygon points="600,740 1200,700 1200,755 600,755" fill="#eef0f3"/>
  </svg>
  <h2 class="heading center" style="top:86px;color:#fff"><span class="h-in">Our Services</span></h2>

  <article class="card" style="left:112px">
    <div class="img" role="img" aria-label="Product team discussing plans around a workshop table" style="background:linear-gradient(135deg,#d4dbe2,#7d93a8 55%,#4a5d72)"></div>
    <div class="icon"><svg width="30" height="30" viewBox="0 0 24 24"><circle cx="12" cy="12" r="4" fill="none" stroke="#fff" stroke-width="2"/><circle cx="12" cy="12" r="9" fill="none" stroke="#fff" stroke-width="2" stroke-dasharray="3 2"/></svg></div>
    <h3>Product Development</h3>
    <p>Lorem ipsum dolor sit amet, consectetur adipiscing elit, sed do eiusmod tempor incididunt ut labore et</p>
  </article>
  <article class="card" style="left:450px">
    <div class="img" role="img" aria-label="Hands reviewing charts on a tablet next to a laptop keyboard" style="background:linear-gradient(135deg,#f1f2f3,#c6cbcf 55%,#8c939a)"></div>
    <div class="icon"><svg width="30" height="30" viewBox="0 0 24 24"><path d="M3 13l4-4 4 3 4-4 6 5-6 5-4-3-4 3z" fill="none" stroke="#fff" stroke-width="2" stroke-linejoin="round"/></svg></div>
    <h3>Brand Development</h3>
    <p>Lorem ipsum dolor sit amet, consectetur adipiscing elit, sed do eiusmod tempor incididunt ut labore et</p>
  </article>
  <article class="card" style="left:789px">
    <div class="img" role="img" aria-label="Man holding a bank card while shopping online at a laptop" style="background:linear-gradient(135deg,#e5e8ea,#9ba9b5 50%,#4b6a8c)"></div>
    <div class="icon"><svg width="30" height="30" viewBox="0 0 24 24"><circle cx="12" cy="12" r="9" fill="none" stroke="#fff" stroke-width="2"/><path d="M3 12h18M12 3c3 3 3 15 0 18M12 3c-3 3-3 15 0 18" fill="none" stroke="#fff" stroke-width="1.6"/></svg></div>
    <h3>Online Positioning</h3>
    <p>Lorem ipsum dolor sit amet, consectetur adipiscing elit, sed do eiusmod tempor incididunt ut labore et</p>
  </article>

  <div class="arrow" style="left:42px"><svg width="14" height="14" viewBox="0 0 14 14"><path d="M9 2L4 7l5 5" fill="none" stroke="#fff" stroke-width="2"/></svg></div>
  <div class="arrow" style="left:1108px"><svg width="14" height="14" viewBox="0 0 14 14"><path d="M5 2l5 5-5 5" fill="none" stroke="#fff" stroke-width="2"/></svg></div>
</section>

<!-- What makes us special -->
<section class="abs special">
  <h2 class="heading center" style="top:92px"><span class="h-in">What makes us special</span></h2>
  <p>We believe that the partners we work for should be able to focus on building their brand and product. Korvath Supply therefore takes care of the process from order processing to delivery. Together with our Partner Korvath Promotional, we can also provide support in the commercial process. We have supplier relationships in more than 30 countries in both the retail and promotional products market.</p>
  <div class="img" role="img" aria-label="Top view of hands typing on a laptop beside a cup of coffee and scattered candies"></div>
</section>

<!-- Blog -->
<h2 class="heading center" style="top:3158px"><span class="h-in">Latest Blog</span></h2>

<article class="abs blog-big">
  <div class="img" role="img" aria-label="Backlit shelves of bottles in a bar"></div>
  <span class="pill" style="left:0;top:317px">Dec-10-2021</span>
  <h4>Lorem ipsum dolor sit amet, consectetur adipiscing elit, sed do Lorem ipsum dolor sit</h4>
  <p>sed do eiusmod tempor incididunt ut labore et dolore magna aliqua. Ut enim ad minim veniam, quis nostrud exercitation ullamco laboris nisi ut aliquip</p>
  <a class="more" style="left:33px;top:538px">Read More ▸</a>
</article>

<article class="abs blog-sm" style="top:3277px">
  <div class="img" role="img" aria-label="Forklift in a warehouse aisle" style="background:linear-gradient(160deg,#6b4a8f,#c07a3a 50%,#3d4b78)"></div>
  <span class="pill">Dec-10-2021</span>
  <h4>Lorem ipsum dolor sit amet, consectetur adipiscing elit, sed do</h4>
  <p>sed do eiusmod tempor incididunt ut labore et dolore magna aliqua. Ut enim ad minim veniam, quis</p>
  <a class="more" style="left:250px;top:227px;font-size:12px">Read More ▸</a>
</article>

<article class="abs blog-sm" style="top:3584px">
  <div class="img" role="img" aria-label="Stacked shipping containers at a port at night" style="background:linear-gradient(160deg,#5a2f2a,#2f4f7a 50%,#1a2a4a)"></div>
  <span class="pill">Dec-10-2021</span>
  <h4>Lorem ipsum dolor sit amet, consectetur adipiscing elit, sed do</h4>
  <p>sed do eiusmod tempor incididunt ut labore et dolore magna aliqua. Ut enim ad minim veniam, quis</p>
  <a class="more" style="left:250px;top:227px;font-size:12px">Read More ▸</a>
</article>

<a class="abs btn" style="left:508px;top:3907px;width:181px;height:50px">View More <b></b></a>

<!-- Partners -->
<h2 class="heading center" style="top:4102px"><span class="h-in">Our Partners</span></h2>
<div class="partner" style="left:110px"><i style="border-radius:50%;background:var(--teal)"></i><span style="color:var(--teal)">Korvath</span></div>
<div class="partner" style="left:345px;font-size:26px">Brinefield</div>
<div class="partner" style="left:556px;font-size:26px">Emberline</div>
<div class="partner" style="left:760px;font-size:26px"><i></i>Kettleworks</div>
<div class="partner" style="left:960px;font-size:26px">Oakhearth</div>

<!-- Footer -->
<div class="abs map" role="img" aria-label="Street map of the office neighbourhood"></div>
<div class="abs addr">Lindenkade 12, 4811 AB<br>Havenstad<br>+31 (0)10 555 0148</div>

<section class="abs contact">
  <h2>CONTACT US</h2>
  <div class="field" style="top:114px">Name</div>
  <div class="field" style="top:178px">Email</div>
  <div class="field" style="top:242px">Message</div>
  <div class="submit">SUBMIT</div>
  <svg class="abs" style="left:232px;top:392px" width="18" height="18" viewBox="0 0 24 24"><path fill="none" stroke="#fff" stroke-width="1.6" d="M6.6 10.8a15 15 0 0 0 6.6 6.6l2.2-2.2a1 1 0 0 1 1-.25 11.4 11.4 0 0 0 3.6.57 1 1 0 0 1 1 1V20a1 1 0 0 1-1 1A17 17 0 0 1 3 4a1 1 0 0 1 1-1h3.5a1 1 0 0 1 1 1c0 1.25.2 2.45.57 3.6a1 1 0 0 1-.25 1z"/></svg>
  <div class="line" style="top:424px">CALL NOW - +31 (0)10 555 0148</div>
  <svg class="abs" style="left:231px;top:469px" width="20" height="15" viewBox="0 0 26 20"><rect x="1" y="1" width="24" height="18" fill="#fff"/><path d="M1 1l12 10L25 1" fill="none" stroke="#2f5f6b" stroke-width="2"/></svg>
  <div class="line" style="top:500px">EMAIL : &nbsp;info@korvathsupply.example</div>
</section>

<div class="abs side" role="img" aria-label="Dimmed close-up of hands typing on a laptop"></div>
<div class="abs copy">© 2021 All Rights Reserved</div>

</body>
</html>
```